Oil Field Service company needs professional business cards

Looking to clean up our current company business cards and look a little more professional. Brenwick Casing Services is a US based company that services the oil field. We deal with engineers, managers and oil rigs....................................................................................................................................................................................................................................................................................................................................................................................................

Target Market(s)

Oil and Gas professionals

Industry/Entity Type

Oil And Gas

Contact Information for Business Card

See attached photo as example

Font styles to use
Sans Serif

Colors
ec1f27

Requirements
Must have
• Company Logo, Name, Title, Cell, Office, Fax, Email.
• See attached photo
Nice to have
• External CRT, Internal CRT, Casing Crews, Torque Turn, Laydown Machine
Should not have
• Do not introduce any new pictures and keep it professional looking

```html
<!DOCTYPE html>
<html lang="en">
<head>
<meta charset="utf-8">
<title>Brenwick Casing Services – Business Card</title>
<link rel="stylesheet" href="https://fonts.googleapis.com/css2?family=Open+Sans:wght@400;600;700&display=swap">
<style>
  :root {
    --brand-red: #e31c23;
    --slate: #45535e;
    --white: #ffffff;
    --page: #ecebea;
    --contact-text: #f1f3f5;
  }
  * { box-sizing: border-box; margin: 0; padding: 0; }
  html, body {
    width: 1200px; height: 900px; overflow: hidden;
    background: var(--page);
    font-family: "Open Sans", Arial, sans-serif;
  }
  .canvas { position: relative; width: 1200px; height: 900px; }

  .card {
    position: absolute;
    width: 556px; height: 344px;
    background: var(--white);
    overflow: hidden;
    box-shadow: 0 6px 18px rgba(0,0,0,0.12);
  }
  .card--front { left: 238px; top: 60px; }
  .card--back  { left: 459px; top: 518px; }

  .card__bands { position: absolute; inset: 0; }

  .front__company {
    position: absolute; top: 44px; left: 0; width: 100%;
    text-align: center;
    font-weight: 700; font-size: 31px; letter-spacing: 3px;
    color: var(--slate);
  }

  .person { position: absolute; top: 230px; right: 319px; text-align: right; color: var(--white); }
  .person__name { font-weight: 700; font-size: 17px; line-height: 22px; }
  .person__title { font-size: 14px; line-height: 20px; color: var(--contact-text); }

  .contacts { position: absolute; top: 212px; left: 270px; list-style: none; }
  .contacts li {
    display: flex; align-items: center; gap: 7px;
    height: 20px; font-size: 14px; color: var(--contact-text);
  }
  .contacts svg { width: 12px; height: 12px; fill: var(--white); flex: none; }

  .services {
    position: absolute; top: 310px; left: 0; width: 100%;
    text-align: center; font-size: 14px; color: var(--contact-text);
  }

  .back__company {
    position: absolute; top: 118px; left: 0; width: 100%;
    text-align: center;
    font-weight: 700; font-size: 34px; line-height: 50px; letter-spacing: 4px;
    color: var(--slate);
  }
</style>
</head>
<body>
<main class="canvas">

  <section class="card card--front" aria-label="Business card front">
    <svg class="card__bands" viewBox="0 0 556 344" width="556" height="344" aria-hidden="true">
      <path fill="var(--brand-red)" d="M0 181 C150 140 220 127 282 127 C350 127 420 140 556 181 L556 195 L0 195 Z"/>
      <rect x="0" y="194" width="556" height="150" fill="var(--slate)"/>
    </svg>

    <p class="front__company">BRENWICK CASING SERVICES</p>

    <div class="person">
      <p class="person__name">Cody Harlan</p>
      <p class="person__title">Area Manager</p>
    </div>

    <ul class="contacts">
      <li>
        <svg viewBox="0 0 24 24" aria-label="Office"><path d="M6.6 10.8a15.1 15.1 0 0 0 6.6 6.6l2.2-2.2c.3-.3.7-.4 1-.2 1.1.4 2.3.6 3.6.6.6 0 1 .4 1 1V20c0 .6-.4 1-1 1A17 17 0 0 1 3 4c0-.6.4-1 1-1h3.5c.6 0 1 .4 1 1 0 1.3.2 2.5.6 3.6.1.3 0 .7-.2 1z"/></svg>
        <span>(555) 410-2200</span>
      </li>
      <li>
        <svg viewBox="0 0 24 24" aria-label="Cell"><path d="M7 1h10a2 2 0 0 1 2 2v18a2 2 0 0 1-2 2H7a2 2 0 0 1-2-2V3a2 2 0 0 1 2-2zm0 3v14h10V4zm5 15.5a1 1 0 1 0 0 2 1 1 0 0 0 0-2z"/></svg>
        <span>(555) 238-9164</span>
      </li>
      <li>
        <svg viewBox="0 0 24 24" aria-label="Fax"><path d="M7 2h8l3 3v4h2a2 2 0 0 1 2 2v9a2 2 0 0 1-2 2H4a2 2 0 0 1-2-2v-9a2 2 0 0 1 2-2h3zm2 2v5h7V6h-2V4zm-3 9v2h2v-2zm4 0v2h2v-2zm4 0v2h2v-2zm-8 4v2h2v-2zm4 0v2h2v-2zm4 0v2h2v-2z"/></svg>
        <span>(555) 410-2201</span>
      </li>
      <li>
        <svg viewBox="0 0 24 24" aria-label="Email"><path d="M2 5h20v14H2zm2 2v.5l8 5 8-5V7zm0 3v7h16v-7l-8 5z"/></svg>
        <span>cody.harlan@brenwickmail.com</span>
      </li>
    </ul>

    <p class="services">Laydown Machine | Casing Crew | Mud Tool | Torque Turn</p>
  </section>

  <section class="card card--back" aria-label="Business card back">
    <p class="back__company">BRENWICK<br>CASING SERVICES</p>
  </section>

</main>
</body>
</html>
```